Private Investment Firm Needs PowerPoint Presentation Template

Design PowerPoint template, take Pinebrook-submitted rough presentation draft, and drop it into new template. See attached Project Brief file for more detail.
Updates

Some decent designs have been submitted but they seem to lack the understanding of our target markets. I am hopeful that more time and feedback will result in better results.

Target Market(s)

Private company owners and intermediaries.

Font styles to use
Serif

Colors
3176b5

Requirements
Must have
• See attached Project Brief.
Nice to have
Should not have
• No B2C fluff--this is a B2B project.

```html
<!DOCTYPE html>
<html lang="en">
<head>
<meta charset="utf-8">
<title>Pinebrook Representative Non-Control Capital Investments</title>
<link rel="stylesheet" href="https://fonts.googleapis.com/css2?family=Figtree:wght@400;600;700&family=Libre+Baskerville:wght@400;700&display=swap">
<style>
  :root {
    --brand-blue: #0870c2;
    --panel-blue: #0a6fc1;
    --ink-dark: #1d1d1d;
    --navy: #1c3f7a;
    --white: #ffffff;
    --mist: #eef1f3;
  }
  html, body {
    margin: 0;
    padding: 0;
    overflow: hidden;
    background: var(--white);
  }
  .slide {
    position: relative;
    width: 1200px;
    height: 676px;
    overflow: hidden;
    background: var(--white);
    font-family: "Figtree", Arial, sans-serif;
  }
  .side-band {
    position: absolute;
    left: 0; top: 0;
    width: 44px; height: 676px;
    background: var(--brand-blue);
  }
  .side-url {
    position: absolute;
    left: 22px; top: 336px;
    transform: translate(-50%, -50%) rotate(-90deg);
    font-family: "Libre Baskerville", Georgia, serif;
    font-size: 13px;
    color: var(--white);
    white-space: nowrap;
  }
  .edge-band {
    position: absolute;
    right: 0; top: 0;
    width: 12px; height: 676px;
    background: var(--brand-blue);
  }
  .page-number {
    position: absolute;
    right: 22px; top: 18px;
    font-family: "Libre Baskerville", Georgia, serif;
    font-size: 17px;
    color: var(--ink-dark);
  }
  .slide-title {
    position: absolute;
    left: 86px; top: 82px;
    margin: 0;
    font-size: 29px;
    line-height: 33px;
    font-weight: 700;
    letter-spacing: 0.3px;
    color: var(--brand-blue);
  }
  .backdrop-photo {
    position: absolute;
    left: 470px; top: 320px;
    width: 718px; height: 356px;
    background: linear-gradient(120deg, rgba(255,255,255,0) 0%, var(--mist) 55%, #e2e7ea 80%, #f4f6f7 100%);
  }
  .case-panel {
    position: absolute;
    left: 45px; top: 230px;
    width: 809px; height: 352px;
    background: var(--panel-blue);
    color: var(--white);
  }
  .case-heading {
    position: absolute;
    left: 41px; top: 26px;
    margin: 0;
    font-size: 42px;
    font-weight: 600;
    letter-spacing: 0.4px;
  }
  .case-points {
    position: absolute;
    left: 41px; top: 94px;
    width: 745px;
    margin: 0; padding: 0;
    list-style: none;
  }
  .case-points li {
    position: relative;
    padding-left: 32px;
    font-size: 17.6px;
    line-height: 28px;
    margin-bottom: 28px;
  }
  .case-points li::before {
    content: "";
    position: absolute;
    left: 1px; top: 9px;
    width: 9px; height: 9px;
    border: 1.5px solid var(--white);
    border-radius: 1px;
  }
  .firm-mark {
    position: absolute;
    left: 68px; top: 622px;
    display: flex;
    align-items: center;
    gap: 10px;
  }
  .firm-mark .dot {
    width: 22px; height: 22px;
    border-radius: 50%;
    background: var(--navy);
  }
  .firm-mark .name {
    font-family: "Libre Baskerville", Georgia, serif;
    font-size: 17px;
    color: var(--navy);
    letter-spacing: 1px;
  }
  .client-mark {
    position: absolute;
    left: 918px; top: 520px;
    width: 224px;
    display: flex;
    flex-direction: column;
    align-items: center;
    gap: 10px;
  }
  .client-mark .block {
    width: 117px; height: 96px;
    background: #1a1a1a;
  }
  .client-mark .name {
    font-size: 17px;
    font-weight: 700;
    letter-spacing: 3px;
    color: var(--ink-dark);
    white-space: nowrap;
  }
</style>
</head>
<body>
<div class="slide">
  <div class="side-band"></div>
  <div class="side-url">www.pinebrookcapital.com</div>
  <div class="edge-band"></div>
  <div class="page-number">14</div>

  <h1 class="slide-title">PINEBROOK REPRESENTATIVE NON-CONTROL<br>CAPITAL INVESTMENTS</h1>

  <div class="backdrop-photo" role="img" aria-label="Faint photograph of white modern architectural columns"></div>

  <section class="case-panel">
    <h2 class="case-heading">Acquisition Finance</h2>
    <ul class="case-points">
      <li>Manufacturer of vibration isolation, seismic control, and shock protection products. The Company’s products are designed to limit the transmission of vibration, impact, seismic, and wind forces to protect larger systems that are at risk of damage from these events.</li>
      <li>Pinebrook’s capital was used to acquire two attractive tuck-in companies (a testing lab and an on-line component distributor) that improved Kestrel’s competitive position. Three years later, the Company set an all-time sales record.</li>
    </ul>
  </section>

  <div class="firm-mark">
    <span class="dot"></span>
    <span class="name">PINEBROOK CAPITAL</span>
  </div>

  <div class="client-mark">
    <span class="block"></span>
    <span class="name">THE KESTREL GROUP</span>
  </div>
</div>
</body>
</html>
```